Create a highly polished design and structured Sales Agreement template

We need a professionally designed Sales Agreement template for our company, Harrowgate Labs, Inc. This template will be used to formalize agreements with our customers for calibration services. The design should reflect the high standards and professionalism of a Keystone 250 company.
Key requirements:
Incorporate our company logo and branding elements.
Ensure the template includes sections for all critical details such as customer name, address, services provided, pricing, and terms of payment.
The layout should be clean, modern, and easy to navigate.
Include placeholders for variable information (e.g., customer name, address, etc.) that can be easily filled out for each customer.
Design the template in a way that allows our team to update it easily via a form entry system.
Ensure the language and formatting are polished and professional.
We have attached our current Sales Agreement for reference. Please maintain all key details while enhancing the structure, format, and overall presentation.

```html
<!DOCTYPE html>
<html lang="en">
<head>
<meta charset="utf-8">
<title>Harrowgate Labs – Facilities Management Service Proposal</title>
<link rel="stylesheet" href="https://fonts.googleapis.com/css2?family=Oswald:wght@500;600&family=Montserrat:wght@500;700;800&family=Open+Sans:wght@400;600;700&display=swap">
<style>
:root{
  --teal:#13958a;
  --teal-soft:rgba(19,149,138,.9);
  --ink:#111;
  --text:#222;
  --stage:#6e6f73;
  --tab-grey:#8e8f93;
  --rule:#cfd1d2;
  --bar:#c9cacb;
  --white:#fff;
}
*{box-sizing:border-box;margin:0;padding:0}
html,body{width:1200px;height:1124px;overflow:hidden;background:var(--stage)}
body{position:relative;font-family:"Open Sans",sans-serif;color:var(--text)}
.page{position:absolute;width:350px;height:495px;background:var(--white);overflow:hidden}
.page-header{position:absolute;left:0;top:0;width:350px;height:30px;background:var(--teal);border-bottom-right-radius:30px;
  display:flex;justify-content:space-between;align-items:center;padding:0 35px 0 19px;color:#e9f6f4;font:400 5.4px "Montserrat",sans-serif;letter-spacing:.1px}
.page-footer{position:absolute;right:0;bottom:0;width:234px;height:17px;background:var(--tab-grey);border-top-left-radius:17px}
.brand{position:absolute;display:flex;align-items:center;gap:4px;color:var(--teal);font:700 7px "Montserrat",sans-serif;letter-spacing:.3px}
.brand-dot{width:12px;height:12px;border-radius:50%;background:#a8a9ab}
.page-title{position:absolute;left:27px;font:800 18px/1 "Montserrat",sans-serif;color:var(--ink)}
.page-title span{display:block;color:var(--teal);font-size:22.5px}
.photo{position:absolute}
/* cover */
.cover-photo{left:198px;top:0;width:152px;height:495px;background:linear-gradient(160deg,#c4c9cb 0%,#8e9596 45%,#6f7775 100%)}
.cover-band{position:absolute;left:0;top:132px;width:282px;height:299px;background:var(--teal-soft)}
.cover-title{position:absolute;left:27px;top:147px;font:600 47px/43px "Oswald",sans-serif;color:var(--white);letter-spacing:-.5px}
.cover-sub{position:absolute;left:27px;top:336px;font:600 27px/26px "Oswald",sans-serif;color:var(--white)}
.cover-url{position:absolute;left:28px;top:464px;font:400 13px "Open Sans",sans-serif;color:#333}
/* toc */
.toc-rule{position:absolute;left:27px;top:110px;width:296px;height:2px;background:var(--teal)}
.toc{position:absolute;left:27px;top:123px;width:285px}
.toc-group{margin-bottom:17px}
.toc-row{display:flex;align-items:center;gap:8px;font:500 6.2px "Montserrat",sans-serif;color:var(--ink);height:12px}
.toc-row.title{font-size:10px;color:var(--teal);height:16px}
.toc-row .lbl{width:97px;flex:none;white-space:nowrap}
.toc-row .lead{flex:1;border-top:1px dashed var(--teal);opacity:.8}
.gears{left:0;top:405px;width:130px;height:90px;background:radial-gradient(circle at 70px 30px,var(--teal) 0 40px,transparent 41px),radial-gradient(circle at 40px 70px,#e1e2e3 0 45px,transparent 46px)}
/* agreement */
.sa-body{position:absolute;left:0;top:110px;width:350px}
.sa-tab{display:inline-block;background:var(--teal);color:var(--white);font:700 9px "Montserrat",sans-serif;padding:2px 12px 2px 20px;margin-bottom:5px}
.sa-sec{margin-bottom:6px}
.sa-text{padding-left:20px;padding-right:24px;font-size:6px;line-height:8px;color:var(--ink)}
.sa-text b{font-weight:700}
.sa-text .num{color:var(--teal);font-weight:700}
.sa-list{list-style:none}
.sa-list li::before{content:"-";display:inline-block;width:11px}
/* content pages */
.black-tab{position:absolute;left:0;width:168px;height:25px;background:var(--ink);border-radius:0 14px 14px 0;color:var(--white);
  font:700 11px "Montserrat",sans-serif;display:flex;align-items:center;padding-left:19px}
.para{position:absolute;font-size:4.7px;line-height:6.3px;color:#333;text-align:justify}
.teal-h{position:absolute;font:700 13px "Montserrat",sans-serif;color:var(--teal)}
.outline{position:absolute;left:19px;top:197px;font:400 9px/12px "Montserrat",sans-serif;color:var(--ink)}
.outline .item{color:var(--teal);font-size:8px}
.outline .sub{padding-left:12px}
.chart{position:absolute;left:160px;top:200px}
.data{position:absolute;left:17px;top:383px;width:316px;border-collapse:collapse;font-size:4.5px;color:#222}
.data th{background:#d7d8d9;color:#fff;font-weight:400;height:15px;text-align:center}
.data th:first-child{text-align:left;padding-left:3px}
.data td{height:14px;border-bottom:1px solid var(--rule);text-align:center}
.data td:first-child{text-align:left;padding-left:3px}
.data .hl{background:var(--teal);color:#fff}
.data .hlc{border-left:1px solid var(--teal);border-right:1px solid var(--teal)}
</style>
</head>
<body>

<!-- Cover -->
<section class="page cover" style="left:65px;top:56px">
  <div class="photo cover-photo" role="img" aria-label="Photo of engineers in safety helmets inspecting equipment on a factory floor"></div>
  <div class="brand" style="left:26px;top:42px;font-size:9px"><span class="brand-dot" style="width:16px;height:16px"></span>HARROWGATE LABS</div>
  <div class="cover-band"></div>
  <h1 class="cover-title">FACILITES<br>MANAGEMENT<br>SERVICE</h1>
  <p class="cover-sub">COMPANY<br>PROPOSAL<br>2024</p>
  <p class="cover-url">www.harrowgatelabs.com</p>
</section>

<!-- Table of contents -->
<section class="page toc-page" style="left:429px;top:56px">
  <header class="page-header"><span>FACILITES MANAGEMENT SERVICE</span><span>COMPANY PROPOSAL 2024</span></header>
  <h2 class="page-title" style="top:56px">TABLE OF<span>CONTANT</span></h2>
  <div class="brand" style="right:28px;top:68px"><span class="brand-dot"></span>HARROWGATE LABS</div>
  <div class="toc-rule"></div>
  <div class="toc">
    <div class="toc-group"><div class="toc-row title"><span class="lbl">1. TITLE GOES HERE</span><span class="lead"></span></div>
      <div class="toc-row"><span class="lbl">1.&nbsp;&nbsp;&nbsp;HEADING GOES HERE</span><span class="lead"></span></div>
      <div class="toc-row"><span class="lbl">2.&nbsp;&nbsp;&nbsp;HEADING GOES HERE</span><span class="lead"></span></div></div>
    <div class="toc-group"><div class="toc-row title"><span class="lbl">2. TITLE GOSE HERE</span><span class="lead"></span></div>
      <div class="toc-row"><span class="lbl">1.&nbsp;&nbsp;&nbsp;HEADING GOES HERE</span><span class="lead"></span></div>
      <div class="toc-row"><span class="lbl">2.&nbsp;&nbsp;&nbsp;HEADING GOES HERE</span><span class="lead"></span></div></div>
    <div class="toc-group"><div class="toc-row title"><span class="lbl">3. TITLE GOSE HERE</span><span class="lead"></span></div>
      <div class="toc-row"><span class="lbl">1.&nbsp;&nbsp;&nbsp;HEADING GOES HERE</span><span class="lead"></span></div>
      <div class="toc-row"><span class="lbl">2.&nbsp;&nbsp;&nbsp;HEADING GOES HERE</span><span class="lead"></span></div></div>
    <div class="toc-group"><div class="toc-row title"><span class="lbl">4. TITLE GOSE HERE</span><span class="lead"></span></div>
      <div class="toc-row"><span class="lbl">1.&nbsp;&nbsp;&nbsp;HEADING GOES HERE</span><span class="lead"></span></div>
      <div class="toc-row"><span class="lbl">2.&nbsp;&nbsp;&nbsp;HEADING GOES HERE</span><span class="lead"></span></div></div>
  </div>
  <div class="photo gears" role="img" aria-label="Decorative illustration of interlocking gears in teal and light grey"></div>
  <div class="page-footer"></div>
</section>

<!-- Sales agreement -->
<section class="page agreement" style="left:790px;top:56px">
  <header class="page-header"><span>FACILITES MANAGEMENT SERVICE</span><span>COMPANY PROPOSAL 2024</span></header>
  <h2 class="page-title" style="left:21px;top:56px">SALES<span>AGREEMENT</span></h2>
  <div class="brand" style="right:22px;top:68px"><span class="brand-dot"></span>HARROWGATE LABS</div>
  <div class="sa-body" style="top:108px">
    <div class="sa-sec"><span class="sa-tab">Seller</span>
      <p class="sa-text">Harrowgate Labs, Inc. 410 Marlow Ridge Rd,<br>Suite B Riverton, ID 83902 Phone: 555-014-2290</p></div>
    <div class="sa-sec"><span class="sa-tab">Customer</span>
      <p class="sa-text">[Customer Name] [Customer Address] [Customer City, State, Zip]<br>Phone: [Customer Phone] Email: [Customer Email]</p></div>
    <div class="sa-sec"><span class="sa-tab">Services</span>
      <p class="sa-text">Harrowgate Labs, Inc. agrees to provide the following services to [Customer Name]:<br>
      <span class="num">1.</span> Calibration Services: Full-time on-site trained technician support.<br>
      <span class="num">2.</span> Turn-key Service Management: Scheduling, on-site calibrations, pick-up and delivery,<br>turn time management, and interface with selected vendors.<br>
      <span class="num">3.</span> Document Control: Online access to calibration documents via our website.</p></div>
    <div class="sa-sec"><span class="sa-tab">Pricing</span>
      <p class="sa-text" style="margin-bottom:8px"><b>Dedicated On-site Technician (3 Days per Week)</b></p>
      <ul class="sa-text sa-list">
        <li>Monthly Charge: $12,500.00</li><li>Yearly Total: $150,000.00</li>
        <li>Sales tax not included.</li><li>Potential annual price increase of 3% beginning the second year.</li></ul></div>
    <div class="sa-sec"><span class="sa-tab">Signatures</span>
      <p class="sa-text"><b>Harrowgate Labs, Inc.</b><br><br>
      [Authorized Signatory Name]<br>[Title]<br>Date: _______________<br>[Customer Name]:<br><br>
      [Authorized Signatory Name]<br>[Title]<br>Date: _______________</p></div>
  </div>
  <div class="page-footer"></div>
</section>

<!-- Content page with chart and table -->
<section class="page content-a" style="left:65px;top:561px">
  <header class="page-header"><span>FACILITES MANAGEMENT SERVICE</span><span>COMPANY PROPOSAL 2024</span></header>
  <h2 class="page-title" style="left:19px;top:57px">HEADING<span>GOES HERE</span></h2>
  <div class="brand" style="right:22px;top:72px"><span class="brand-dot"></span>HARROWGATE LABS</div>
  <div class="black-tab" style="top:108px">HEADING GOES HERE</div>
  <p class="para" style="left:19px;top:139px;width:310px;text-align:left">Lorem ipsum dolor sit amet, consectetur adipiscing elit, sed do eiusmod tempor incididunt ut labore et dolore magna aliqua. Ut enim ad minim veniam, quis nostrud exercitation ullamco laboris nisi ut aliquip ex ea commodo consequat. Duis aute irure dolor in reprehenderit in voluptate velit esse cillum dolore eu fugiat nulla pariatur. Excepteur sint occaecat cupidatat non proident, sunt in culpa qui officia deserunt mollit anim id est laborum.Lorem ipsum dolor sit amet, consectetur adipiscing elit, sed do eiusmod tempor incididunt ut labore et dolore magna aliqua. Ut enim ad minim veniam, quis nostrud exercitation ullamco laboris nisi ut aliquip ex ea commodo consequat. Duis aute irure dolor in reprehenderit in voluptate velit esse cillum dolore eu fugiat nulla pariatur. Excepteur sint occaecat</p>
  <div class="outline">
    <div class="item">1.&nbsp;&nbsp;HEADING GOES HERE</div>
    <div class="sub">a) Lorem ipsum</div><div class="sub">b) Lorem ipsum</div>
    <div class="item" style="margin-top:4px">2.&nbsp;&nbsp;HEADING GOES HERE</div>
    <div class="sub">a) Lorem ipsum</div><div class="sub">b) Lorem ipsum</div><div class="sub">c) Lorem ipsum</div><div class="sub">d) Lorem ipsum</div>
  </div>
  <svg class="chart" width="175" height="90" viewBox="0 0 175 90" font-family="Open Sans, sans-serif">
    <text x="84" y="10" font-size="8" fill="#444" text-anchor="middle">Temperature in well 20 in °C</text>
    <g font-size="4.2" fill="#666" text-anchor="end">
      <text x="8" y="21">140</text><text x="8" y="29">120</text><text x="8" y="37">100</text><text x="8" y="45">80</text>
      <text x="8" y="53">60</text><text x="8" y="61">40</text><text x="8" y="69">20</text><text x="8" y="77">0</text></g>
    <g stroke="#e3e4e5" stroke-width=".5">
      <line x1="12" y1="20" x2="160" y2="20"/><line x1="12" y1="28" x2="160" y2="28"/><line x1="12" y1="36" x2="160" y2="36"/>
      <line x1="12" y1="44" x2="160" y2="44"/><line x1="12" y1="52" x2="160" y2="52"/><line x1="12" y1="60" x2="160" y2="60"/>
      <line x1="12" y1="68" x2="160" y2="68"/><line x1="12" y1="76" x2="160" y2="76"/></g>
    <g fill="var(--bar)">
      <rect x="16" y="54" width="8" height="22"/><rect x="30" y="59" width="8" height="17"/><rect x="45" y="42" width="8" height="34"/>
      <rect x="59" y="40" width="8" height="36"/><rect x="74" y="37" width="8" height="39"/><rect x="88" y="31" width="8" height="45"/>
      <rect x="103" y="27" width="8" height="49"/><rect x="117" y="26" width="8" height="50"/><rect x="132" y="25" width="8" height="51"/></g>
    <g font-size="4.2" fill="#555" text-anchor="middle">
      <text x="20" y="52">56</text><text x="34" y="57">42</text><text x="49" y="40">86</text><text x="63" y="38">90</text>
      <text x="78" y="35">98</text><text x="92" y="29">115</text><text x="107" y="25">125</text><text x="121" y="24">127</text><text x="136" y="23">129</text>
      <text x="20" y="84">2000</text><text x="34" y="84">2002</text><text x="49" y="84">2003</text><text x="63" y="84">2004</text>
      <text x="78" y="84">2005</text><text x="92" y="84">2006</text><text x="107" y="84">2007</text><text x="121" y="84">2008</text><text x="136" y="84">2009</text></g>
  </svg>
  <div class="black-tab" style="top:305px">HEADING GOES HERE</div>
  <p class="para" style="left:19px;top:337px;width:310px;text-align:left">Lorem ipsum dolor sit amet, consectetur adipiscing elit, sed do eiusmod tempor incididunt ut labore et dolore magna aliqua. Ut enim ad minim veniam, quis nostrud exercitation ullamco laboris nisi ut aliquip ex ea commodo consequat. Duis aute irure dolor in reprehenderit in voluptate velit esse cillum dolore eu fugiat nulla pariatur. Excepteur sint occaecat cupidatat non proident, sunt in culpa qui officia deserunt mollit anim id est laborum.Lorem ipsum dolor sit amet, consectetur adipiscing elit, sed do eiusmod tempor incididunt ut labore et dolore magna aliqua.</p>
  <table class="data">
    <thead><tr><th style="width:96px">Heading Goes Here</th><th class="hl">Heading<br>Goes Here</th><th>Heading<br>Goes Here</th><th>Heading<br>Goes Here</th><th>Heading<br>Goes Here</th></tr></thead>
    <tbody>
      <tr><td>Lorem Ipsum Goes Here</td><td class="hlc">23</td><td>12</td><td>78</td><td>12</td></tr>
      <tr><td>Lorem Ipsum Goes Here</td><td class="hlc">45</td><td>56</td><td>12</td><td>56</td></tr>
      <tr><td>Lorem Ipsum Goes Here</td><td class="hlc">78</td><td>76</td><td>34</td><td>76</td></tr>
      <tr><td>Lorem Ipsum Goes Here</td><td class="hlc" style="border-bottom:1px solid var(--teal)">22</td><td>12</td><td>55</td><td>12</td></tr>
    </tbody>
  </table>
  <div class="page-footer"></div>
</section>

<!-- Content page, two columns -->
<section class="page content-b" style="left:429px;top:561px">
  <header class="page-header"><span>FACILITES MANAGEMENT SERVICE</span><span>COMPANY PROPOSAL 2024</span></header>
  <h2 class="page-title" style="left:19px;top:49px">HEADING<span>GOES HERE</span></h2>
  <div class="brand" style="right:22px;top:64px"><span class="brand-dot"></span>HARROWGATE LABS</div>
  <h3 class="teal-h" style="left:19px;top:102px">HEADING GOES HERE</h3>
  <p class="para" style="left:19px;top:124px;width:147px">Lorem ipsum dolor sit amet, consectetuer adipiscing elit, sed diam nonummy nibh euismod tincidunt ut laoreet dolore magna aliquam erat volutpat. Ut wisi enim ad minim veniam, quis nostrud exerci tation ullamcorper suscipit lobortis nisl ut aliquip ex ea commodo consequat. Duis autem vel eum iriure dolor in hendrerit in vulputate velit esse molestie consequat, vel illum dolore eu feugiat nulla facilisis at vero eros et accumsan et iusto odio dignissim qui blandit praesent luptatum zzril delenit augue duis dolore te feugait nulla facilisi.<br><br>Lorem ipsum dolor sit amet, cons ectetuer adipiscing elit, sed diam nonummy nibh euismod tincidunt ut laoreet dolore magna aliquam erat volutpat. Ut wisi enim ad minim veniam, quis nostrud exerci tation ullamcorper suscipit lobortis nisl ut aliquip ex ea commodo consequat.<br><br>Lorem ipsum dolor sit amet, consectetuer adipiscing elit, sed diam nonummy nibh euismod tincidunt ut laoreet dolore magna aliquam erat volutpat. Ut wisi enim ad minim veniam, quis nostrud exerci tation ullamcorper suscipit lobortis nisl ut aliquip ex ea com elit, sed diam nonummy nibh euismod tincidunt ut laoreet dolore magna aliquam erat volutpat. Ut wisi enim ad</p>
  <div class="photo" style="left:19px;top:306px;width:144px;height:90px;background:linear-gradient(135deg,#d9dee2,#8d969c 55%,#3d4650)" role="img" aria-label="Photo of colleagues smiling during a meeting at a table"></div>
  <p class="para" style="left:19px;top:405px;width:147px">Lorem ipsum dolor sit amet, cons ectetuer adipiscing elit, sed diam nonummy nibh euismod tincidunt ut laoreet dolore magna aliquam erat volutpat. Ut wisi enim ad minim veniam, quis nostrud exerci tation ullamcorper suscipit lobortis nisl ut aliquip ex ea commodo consequat.</p>
  <h3 class="teal-h" style="left:185px;top:101px">HEADING GOES HERE</h3>
  <p class="para" style="left:185px;top:121px;width:147px">Lorem ipsum dolor sit amet, consectetuer adipiscing elit, sed diam nonummy nibh euismod tincidunt ut laoreet dolore magna aliquam erat volutpat. Ut wisi enim ad minim veniam, quis nostrud exerci tation ullamcorper suscipit lobortis nisl ut aliquip ex ea commodo consequat. Duis autem vel eum iriure dolor in hendrerit in vulputate velit esse molestie consequat, vel illum dolore eu feugiat nulla facilisis at vero eros et accumsan et iusto odio dignissim qui blandit praesent luptatum zzril delenit augue duis dolore te feugait nulla facilisi.<br><br>Lorem ipsum dolor sit amet, cons ectetuer adipiscing elit, sed diam nonummy nibh euismod tincidunt ut laoreet dolore magna aliquam erat volutpat. Ut wisi enim ad minim veniam, quis nostrud exerci tation ullamcorper suscipit lobortis nisl ut aliquip ex ea commodo consequat.<br><br>Lorem ipsum dolor sit amet, consectetuer adipiscing elit, sed diam nonummy nibh euismod tincidunt ut laoreet dolore magna aliquam erat volutpat. Ut wisi enim ad minim veniam, quis nostrud exerci tation ullamcorper suscipit lobortis nisl ut aliquip ex ea com elit, sed diam nonummy nibh euismod tincidunt ut laoreet dolore magna aliquam erat volutpat. Ut wisi enim ad</p>
  <h3 class="teal-h" style="left:185px;top:305px">HEADING GOES HERE</h3>
  <p class="para" style="left:185px;top:326px;width:147px">Lorem ipsum dolor sit amet, consectetuer adipiscing elit, sed diam nonummy nibh euismod tincidunt ut laoreet dolore magna aliquam erat volutpat. Ut wisi enim ad minim veniam, quis nostrud exerci tation ullamcorper suscipit lobortis nisl ut aliquip ex ea commodo consequat. Duis autem vel eum iriure dolor in hendrerit in vulputate velit esse molestie consequat, vel illum dolore eu feugiat nulla facilisis at vero eros et accumsan et iusto odio dignissim qui blandit praesent luptatum zzril delenit augue duis dolore te feugait nulla facilisi.<br><br>Lorem ipsum dolor sit amet, cons ectetuer adipiscing elit, sed diam nonummy nibh euismod tincidunt ut laoreet dolore magna aliquam erat volutpat. Ut wisi enim ad minim veniam, quis nostrud exerci tation ullamcorper suscipit lobortis nisl ut aliquip ex ea commodo consequat.</p>
  <div class="page-footer"></div>
</section>

<!-- Content page, single column -->
<section class="page content-c" style="left:792px;top:561px">
  <header class="page-header"><span>FACILITES MANAGEMENT SERVICE</span><span>COMPANY PROPOSAL 2024</span></header>
  <h2 class="page-title" style="left:19px;top:49px">HEADING<span>GOES HERE</span></h2>
  <div class="brand" style="right:22px;top:64px"><span class="brand-dot"></span>HARROWGATE LABS</div>
  <h3 class="teal-h" style="left:19px;top:102px">HEADING GOES HERE</h3>
  <p class="para" style="left:19px;top:124px;width:301px">Lorem ipsum dolor sit amet, consectetuer adipiscing elit, sed diam nonummy nibh euismod tincidunt ut laoreet dolore magna aliquam erat volutpat. Ut wisi enim ad minim veniam, quis nostrud exerci tation ullamcorper suscipit lobortis nisl ut aliquip ex ea commodo consequat. Duis autem vel eum iriure dolor in hendrerit in vulputate velit esse molestie consequat, vel illum dolore eu feugiat nulla facilisis at vero eros et accumsan et iusto odio dignissim qui blandit praesent luptatum zzril delenit augue duis dolore te feugait nulla facilisi.<br>Lorem ipsum dolor sit amet, cons ectetuer adipiscing elit, sed diam nonummy nibh euismod tincidunt ut laoreet dolore magna aliquam erat volutpat. Ut wisi enim ad minim veniam, quis nostrud exerci tation ullamcorper suscipit lobortis nisl ut aliquip ex ea commodo consequat.<br>Lorem ipsum dolor sit amet, consectetuer adipiscing elit, sed diam nonummy nibh euismod tincidunt ut laoreet dolore magna aliquam erat volutpat. Ut wisi enim ad minim veniam, quis nostrud exerci tation ullamcorper suscipit lobortis nisl ut aliquip ex ea com elit, sed diam nonummy nibh euismod tincidunt ut laoreet dolore magna aliquam erat volutpat. Ut wisi enim ad Lorem ipsum dolor sit amet, consectetuer adipiscing elit, sed diam nonummy nibh euismod tincidunt ut laoreet dolore magna aliquam erat volutpat. Ut wisi enim ad minim veniam, quis nostrud exerci tation ullamcorper suscipit lobortis nisl ut aliquip ex ea com elit, sed diam nonummy nibh euismod tincidunt ut laoreet dolore magna aliquam erat volutpat. Ut wisi enim ad</p>
  <h3 class="teal-h" style="left:19px;top:222px">HEADING GOES HERE</h3>
  <p class="para" style="left:19px;top:244px;width:301px">Lorem ipsum dolor sit amet, consectetuer adipiscing elit, sed diam nonummy nibh euismod tincidunt ut laoreet dolore magna aliquam erat volutpat. Ut wisi enim ad minim veniam, quis nostrud exerci tation ullamcorper suscipit lobortis nisl ut aliquip ex ea commodo consequat. Duis autem vel eum iriure dolor in hendrerit in vulputate velit esse molestie consequat, vel illum dolore eu feugiat nulla facilisis at vero eros et accumsan et iusto odio dignissim qui blandit praesent luptatum zzril delenit augue duis dolore te feugait nulla facilisi.<br>Lorem ipsum dolor sit amet, cons ectetuer adipiscing elit, sed diam nonummy nibh euismod tincidunt ut laoreet dolore magna aliquam erat volutpat. Ut wisi enim ad minim veniam, quis nostrud exerci tation ullamcorper suscipit lobortis nisl ut aliquip ex ea commodo consequat.</p>
  <h3 class="teal-h" style="left:19px;top:302px">HEADING GOES HERE</h3>
  <p class="para" style="left:19px;top:324px;width:301px">Lorem ipsum dolor sit amet, consectetuer adipiscing elit, sed diam nonummy nibh euismod tincidunt ut laoreet dolore magna aliquam erat volutpat. Ut wisi enim ad minim veniam, quis nostrud exerci tation ullamcorper suscipit lobortis nisl ut aliquip ex ea commodo consequat. Duis autem vel eum iriure dolor in hendrerit in vulputate velit esse molestie consequat, vel illum dolore eu feugiat nulla facilisis at vero eros et accumsan et iusto odio dignissim qui blandit praesent luptatum zzril delenit augue duis dolore te feugait nulla facilisi.</p>
  <div class="photo" style="left:19px;top:371px;width:312px;height:75px;background:linear-gradient(90deg,#7f8c90 0%,#a5795d 30%,#2f7f8f 58%,#c9d6de 100%)" role="img" aria-label="Strip of four photos of industrial laboratory and processing equipment"></div>
  <div class="page-footer"></div>
</section>

</body>
</html>
```